Graphic background for 10 Pull Up Banners

To produce a graphic background for a 100 cm wide by 200 cm high Pull-Up Display banner containing a Buddhist text in three languages: Tibetan, Mandarin and English. Please refer to uploaded file "Elements of Pull Up Banner". The design should be simple (not drawing attention away from the text). This design should then be varied for or extended to the next banner and so on until the 10th banner. When the banners are lined up, they should form a single design that is 1000 cm wide by 200 cm high.
An alternative way to look at the project is to produce a graphic background of 1000 cm width by 200 cm height that is then splitted into ten separate 100 cm wide by 200 cm high graphic to be used as background for 10 Buddhist texts (text 1, 2, 3, 4, 5, 6, 7, 8, 9a, 9b) on 10 Pull-Up Display Banners, the text in each banner being in the three languages mentioned earlier.
In either perspective, the design should be simple and not draw attention away from the texts. See uploaded PDF file "Examples.pdf"
Target Market(s)
For attendees at a Buddhist Event.
Look and feel
Each slider illustrates characteristics of the customer's brand and the style your logo design should communicate.

```html
<!DOCTYPE html>
<html lang="en">
<head>
<meta charset="utf-8">
<title>Pull-Up Banners – Ten Mistaking and Desire &amp; Attachment</title>
<link href="https://fonts.googleapis.com/css2?family=Crimson+Pro:wght@500;600&family=Noto+Serif+SC:wght@400;600&family=Noto+Serif+Tibetan&family=Arimo&display=swap" rel="stylesheet">
<style>
  :root {
    --green-top: #9fd05a;
    --green-mid: #b6d948;
    --yellow-low: #d9e22c;
    --frame: #ffffff;
    --crimson: #c2143c;
    --text-red: #cc3b4c;
    --box-fill: rgba(255, 255, 255, 0.24);
    --box-line: rgba(255, 255, 255, 0.45);
    --art-a: #c9c46a;
    --art-b: #b88f55;
  }
  * { margin: 0; padding: 0; box-sizing: border-box; }
  html, body { width: 1200px; height: 1200px; overflow: hidden; background: #ffffff; }
  .canvas { position: relative; width: 1200px; height: 1200px; display: flex; }
  .banner {
    position: relative; width: 600px; height: 1200px; overflow: hidden;
    background: linear-gradient(180deg, var(--green-top) 0%, var(--green-mid) 55%, var(--yellow-low) 100%);
  }
  .banner + .banner { border-left: 1px solid rgba(255,255,255,0.35); }
  .banner__waves, .banner__frame { position: absolute; inset: 0; width: 600px; height: 1200px; }
  .deity-art {
    position: absolute; top: 60px; width: 120px; height: 136px;
    background: radial-gradient(ellipse at 50% 45%, var(--art-a) 0%, var(--art-b) 75%, transparent 100%);
    border-radius: 40% 40% 8px 8px; opacity: 0.75;
  }
  .title {
    position: absolute; font-family: "Crimson Pro", serif; font-weight: 600;
    color: var(--crimson); line-height: 1; letter-spacing: -0.5px;
  }
  .text-box {
    position: absolute; background: var(--box-fill);
    display: flex; flex-direction: column; justify-content: center; align-items: center;
    text-align: center; color: var(--text-red);
  }
  .tibetan { font-family: "Noto Serif Tibetan", serif; }
  .chinese { font-family: "Noto Serif SC", serif; }
  .english { font-family: "Arimo", sans-serif; }
  .dedication {
    position: absolute; background: var(--box-fill);
    display: flex; flex-direction: column; justify-content: center; align-items: center; gap: 6px;
    text-align: center;
  }
  .dedication::before {
    content: ""; position: absolute; inset: 9px; border: 1px solid var(--box-line);
  }
  .dedication__tibetan { font-size: 12px; color: var(--text-red); }
  .dedication__chinese { font-size: 13px; font-weight: 600; color: var(--crimson); }
  .dedication__english { font-family: "Crimson Pro", serif; font-weight: 500; font-size: 13px; color: var(--crimson); }

  /* Ten Mistaking */
  .mistaking .deity-art { left: 82px; }
  .mistaking .title { left: 206px; top: 92px; font-size: 62px; }
  .mistaking .box-tibetan { left: 115px; top: 236px; width: 368px; height: 208px; font-size: 6.5px; line-height: 14px; }
  .mistaking .box-chinese { left: 115px; top: 476px; width: 368px; height: 208px; font-size: 12px; line-height: 15px; }
  .mistaking .footnotes { margin-top: 14px; font-size: 5px; line-height: 7px; font-style: italic; }
  .mistaking .box-english { left: 115px; top: 720px; width: 368px; height: 208px; font-size: 7.4px; line-height: 15.6px; }
  .mistaking .dedication { left: 140px; top: 1012px; width: 320px; height: 124px; }

  /* Desire & Attachment */
  .desire .deity-art { left: 82px; }
  .desire .title--desire { left: 270px; top: 72px; font-size: 58px; }
  .desire .title--amp { left: 434px; top: 106px; font-size: 34px; }
  .desire .title--attachment { left: 222px; top: 134px; font-size: 58px; }
  .desire .box-tibetan { left: 116px; top: 236px; width: 370px; height: 208px; font-size: 8.5px; line-height: 29px; }
  .desire .box-chinese { left: 116px; top: 478px; width: 370px; height: 208px; font-size: 21.5px; line-height: 28px; letter-spacing: 1.5px; }
  .desire .box-english { left: 116px; top: 722px; width: 370px; height: 208px; font-size: 12px; line-height: 31.5px; }
  .desire .dedication { left: 140px; top: 1018px; width: 322px; height: 120px; }
</style>
</head>
<body>
<main class="canvas">

  <section class="banner mistaking" aria-label="Banner: Ten Mistaking">
    <svg class="banner__waves" viewBox="0 0 600 1200" aria-hidden="true">
      <path d="M0 980 C150 930 300 1010 600 940 L600 1200 L0 1200 Z" fill="#e6e43a" opacity="0.35"/>
      <path d="M0 1040 C180 990 360 1070 600 1010" fill="none" stroke="#f3ee6a" stroke-width="3" opacity="0.5"/>
      <path d="M0 1070 C200 1020 380 1110 600 1050" fill="none" stroke="#f3ee6a" stroke-width="2" opacity="0.4"/>
      <path d="M0 1110 C220 1060 380 1150 600 1090 L600 1200 L0 1200 Z" fill="#e2b832" opacity="0.3"/>
    </svg>
    <svg class="banner__frame" viewBox="0 0 600 1200" aria-hidden="true">
      <path d="M84 18 H511 A68 68 0 0 0 579 86 V1114 A68 68 0 0 0 511 1182 H84 A68 68 0 0 0 16 1114 V86 A68 68 0 0 0 84 18 Z" fill="none" stroke="var(--frame)" stroke-width="3"/>
    </svg>
    <div class="deity-art" role="img" aria-label="Seated Buddhist deity line illustration on a lotus throne"></div>
    <h1 class="title">Ten Mistaking</h1>

    <div class="text-box box-tibetan tibetan" lang="bo">
      <p>དད་པ་ དང་ འདོད་ཆགས་ འཁྲུལ།</p>
      <p>སྙིང་རྗེ་ དང་ ཞེན་པ་ འཁྲུལ།</p>
      <p>སྟོང་ཉིད་ དང་ རྟོག་པ་ འཁྲུལ།</p>
      <p>ཆོས་དབྱིངས་ དང་ ཆད་ལྟ་ འཁྲུལ།</p>
      <p>ཉམས་ དང་ རྟོགས་པ་ འཁྲུལ།</p>
      <p>ཆོས་པ་ དང་ སྒྲུབ་པ་ འཁྲུལ།</p>
      <p>བདུད་ དང་ གྲོལ་བ་ འཁྲུལ།</p>
      <p>གྲུབ་ཐོབ་ དང་ གཡོ་ཅན་ འཁྲུལ།</p>
      <p>གཞན་དོན་ དང་ རང་དོན་ འཁྲུལ།</p>
      <p>ཐབས་ དང་ གཡོ་སྒྱུ་ འཁྲུལ།</p>
    </div>

    <div class="text-box box-chinese chinese" lang="zh">
      <p>信心与爱欲可能混淆，</p>
      <p>慈悲与贪执可能混淆，</p>
      <p>所知<sup>1</sup>本空与思维造作空性可能混淆，</p>
      <p>法界与断见<sup>2</sup>可能混淆，</p>
      <p>觉受与证悟可能混淆，</p>
      <p>尊者与神棍可能混淆，</p>
      <p>破惑与着魔可能混淆，</p>
      <p>成就者与骗子可能混淆，</p>
      <p>利他与自利可能混淆，</p>
      <p>方便善巧与谄媚哄骗可能混淆。</p>
      <div class="footnotes">
        <p>1. 所知：可以认识的事物。</p>
        <p>2. 断见：否定因果、前生、后世等流的见解。</p>
      </div>
    </div>

    <div class="text-box box-english english">
      <p>Desire can be mistaken for faith or devotion.</p>
      <p>Attachment can be mistaken for love and compassion.</p>
      <p>Conceptual emptiness can be mistaken for the emptiness of the nature of phenomena.</p>
      <p>Nihilism can be mistaken for the dharmadhatu.</p>
      <p>A meditative experience can be mistaken for realization.</p>
      <p>Outer religious practices can be mistaken for inner development of good qualities.</p>
      <p>A person in the grip of a demon can be mistaken for a person who has destroyed his own delusions.</p>
      <p>A charlatan can be mistaken for a siddha.</p>
      <p>An act to benefit yourself can be mistaken for an act to benefit others.</p>
      <p>Deviousness can be mistaken for skilful means.</p>
    </div>

    <div class="dedication">
      <p class="dedication__tibetan tibetan" lang="bo">སེམས་ཅན་ ཀུན་ སངས་རྒྱས་ ཐོབ་པར་ ཤོག།</p>
      <p class="dedication__chinese chinese" lang="zh">愿诸有情共证佛果位</p>
      <p class="dedication__english">May all attain Buddhahood together.</p>
    </div>
  </section>

  <section class="banner desire" aria-label="Banner: Desire and Attachment">
    <svg class="banner__waves" viewBox="0 0 600 1200" aria-hidden="true">
      <path d="M0 940 C260 1010 420 930 600 990 L600 1200 L0 1200 Z" fill="#e6e43a" opacity="0.35"/>
      <path d="M0 1010 C240 1070 420 990 600 1050" fill="none" stroke="#f3ee6a" stroke-width="3" opacity="0.5"/>
      <path d="M0 1050 C220 1110 420 1030 600 1090" fill="none" stroke="#f3ee6a" stroke-width="2" opacity="0.4"/>
      <path d="M0 1090 C220 1150 420 1070 600 1120 L600 1200 L0 1200 Z" fill="#e2c034" opacity="0.3"/>
    </svg>
    <svg class="banner__frame" viewBox="0 0 600 1200" aria-hidden="true">
      <path d="M84 18 H514 A68 68 0 0 0 582 86 V1114 A68 68 0 0 0 514 1186 H84 A68 68 0 0 0 16 1118 V86 A68 68 0 0 0 84 18 Z" fill="none" stroke="var(--frame)" stroke-width="3"/>
    </svg>
    <div class="deity-art" role="img" aria-label="Seated Buddhist deity line illustration on a lotus throne"></div>
    <h1 class="title title--desire">Desire</h1>
    <span class="title title--amp">&amp;</span>
    <span class="title title--attachment">Attachment</span>

    <div class="text-box box-tibetan tibetan" lang="bo">
      <p>འདོད་པ་ མེད་ན་ རང་དོན་ མི་འགྲུབ།</p>
      <p>འདོད་པ་ ཐམས་ཅད་ ཞེན་པ་ མིན།</p>
      <p>འདོད་ཞེན་ ཁྱད་པར་ མི་ཤེས་ ན།</p>
      <p>ཉོན་མོངས་ ལམ་དུ་ ཁྱེར་བ་ ཧ་ཅང་ངོ་།</p>
    </div>

    <div class="text-box box-chinese chinese" lang="zh">
      <p>若无意欲则不成自利，</p>
      <p>然有意欲非为执着故，</p>
      <p>不知意欲执着差别即，</p>
      <p>贪执说所当取确荒唐。</p>
    </div>

    <div class="text-box box-english english">
      <p>If you have no desire, your goal cannot be achieved.</p>
      <p>Since not all desire is attachment,</p>
      <p>not knowing how to differentiate desire from attachment,</p>
      <p>to talk about bringing passion into the path is absurd.</p>
    </div>

    <div class="dedication">
      <p class="dedication__tibetan tibetan" lang="bo">སེམས་ཅན་ ཀུན་ སངས་རྒྱས་ ཐོབ་པར་ ཤོག།</p>
      <p class="dedication__chinese chinese" lang="zh">愿诸有情共证佛果位</p>
      <p class="dedication__english">May all attain Buddhahood together.</p>
    </div>
  </section>

</main>
</body>
</html>
```